Aquatic View

We need a web design for a new window cleaning company name Tidewell Glass Care. We are located in Grand Cayman, Cayman Islands. We are a small company, a team of husband and wife. Our services include residencial interior and exterior window cleaning and commercial. Extra services such as ceiling fans cleaning, mirrors, high dusting. Home cleaning services. Power washing. Explaining the service. We want a modern, beachy style with aquatic colors. We want to use our domain name "tidewellglasscare.ky". We want to portray a clean, modern and professional design.

Target Market(s)

Big Home owners

Industry/Entity Type

Cleaning Service

Contact Information for Business Card

Company Name: Tidewell Glass Care
Name: Desmond Farrowby owner/manager
Phone: 345-9170452
Email: desmond@tidewellglasscare.ky
Website: tidewellglasscare.ky
Address: P.O.Box 2486 GT, George Town, Grand Cayman KY1-1203 Cayman Islands

Number of Pages Required

2 page

Font styles to use
Sans Serif

Colors
0592cd
0455a3
33a6d7
85cae6
cadf82
abd036
fbf289

Requirements
Nice to have
• Pictures of an ocean view and palm trees from clear windows.
• https://quorvantel.com/bidlinker/
• Use the above for "free estimate".

```html
<!DOCTYPE html>
<html lang="en">
<head>
<meta charset="utf-8">
<title>Tidewell Glass Care</title>
<link rel="stylesheet" href="https://fonts.googleapis.com/css2?family=Roboto:wght@300;400;500;700&family=Oswald:wght@400;500&family=Open+Sans:wght@400;600&display=swap">
<style>
:root{
  --ocean:#0592cd;
  --deep:#0455a3;
  --sky:#33a6d7;
  --mist:#85cae6;
  --ink:#333333;
  --muted:#777777;
  --card-bg:#f2f6f8;
  --card-line:#d3dde2;
  --footer:#1c1c1c;
  --footer-base:#131313;
  --footer-text:#d6d6d6;
}
*{margin:0;padding:0;box-sizing:border-box}
html,body{width:1200px;height:2314px;overflow:hidden}
body{position:relative;background:#fff;font-family:'Roboto',sans-serif;color:var(--ink)}
.abs{position:absolute}

/* top bar */
.topbar{left:0;top:0;width:1200px;height:38px;background:var(--ocean);color:#fff;font-size:12px}
.topbar span{position:absolute;top:12px}
.topbar svg{vertical-align:-1px}

/* hero backdrop */
.hero-backdrop{left:0;top:38px;width:1200px;height:664px;
  background:linear-gradient(180deg,#eef6fb 0%,#d7ecf6 30%,#a9d9ee 55%,#6fc2e2 68%,#c6e6f2 85%,#fff 100%)}

/* header */
.brand{left:99px;top:64px;display:flex;align-items:center;gap:8px;font-weight:700;font-size:17px;color:var(--deep)}
.brand .dot{width:26px;height:26px;border-radius:50%;background:var(--ocean)}
.nav{top:77px;right:99px;display:flex;align-items:center;font-size:13px;font-weight:500;color:#333}
.nav a{color:inherit;text-decoration:none;padding:0 18px}
.nav a.active{color:var(--ocean)}
.nav .slash{width:1px;height:30px;background:#999;transform:rotate(22deg)}

/* slider */
.slider{left:99px;top:136px;width:1002px;height:530px}
.slider-title{left:0;top:484px;width:1200px;text-align:center;font-family:'Oswald',sans-serif;font-size:33px;color:var(--ocean);text-shadow:0 0 3px #fff,0 0 3px #fff;letter-spacing:0.5px}
.search{left:353px;top:551px;width:494px;height:44px;display:flex}
.search .field{flex:1;background:#fff;font-size:12px;color:#888;padding:14px 19px}
.search .go{width:85px;background:var(--ocean);color:#fff;font-size:12px;font-weight:500;display:flex;align-items:center;justify-content:center}
.pager{left:566px;top:618px;width:68px;height:26px;background:#fff;border-radius:13px;display:flex;justify-content:space-around;align-items:center}

/* welcome */
.welcome-title{left:0;top:714px;width:1200px;text-align:center;font-size:26px;font-weight:500;color:#333}
.welcome-text{left:190px;top:758px;width:820px;text-align:center;font-size:12px;line-height:20px;color:var(--muted)}
.down{left:586px;top:816px;width:28px;height:36px;border:1px solid #cfd8dc;border-radius:5px;display:flex;align-items:center;justify-content:center;background:#fff}

/* services */
.service{top:862px;width:314px;height:400px}
.service .head{position:absolute;left:0;top:0}
.service .title{position:absolute;left:0;top:56px;width:314px;text-align:center;color:#fff;font-size:18px}
.service .body{position:absolute;left:0;top:98px;width:314px;height:302px;background:var(--card-bg);border:1px solid var(--card-line);border-top:none}
.service .icon{position:absolute;left:117px;top:26px;width:80px;height:82px}
.service p{position:absolute;left:24px;top:142px;width:266px;text-align:center;font-size:12px;line-height:20px;color:#444}
.btn{display:flex;align-items:center;justify-content:center;background:var(--deep);color:#fff;font-size:12px;font-weight:700;border-radius:4px}
.service .btn{position:absolute;left:109px;top:238px;width:97px;height:36px}

/* about */
.about-title{left:99px;top:1318px;font-size:26px;font-weight:500}
.about-text{left:99px;top:1370px;width:510px;font-size:12px;line-height:20px;color:#555}
.about-btn{left:99px;top:1536px;width:91px;height:36px}
.video{left:651px;top:1326px;width:449px;height:244px;background:linear-gradient(120deg,#3d4a3c 0%,#5d6a62 40%,#6f7b83 70%,#4e5a4c 100%);border:2px solid #e8e8e8}
.play{left:837px;top:1411px;width:78px;height:78px;border-radius:50%;background:rgba(255,255,255,0.85);display:flex;align-items:center;justify-content:center}

/* gallery */
.gallery-title{left:0;top:1622px;width:1200px;text-align:center;font-size:26px;font-weight:500}
.shot{top:1706px;height:210px;border:4px solid #fff;box-shadow:0 0 0 1px #e5e5e5}
.g1{left:99px;width:324px;background:linear-gradient(160deg,#dfeef7 0%,#4f86b8 45%,#9ec3dc 70%,#e8f1f6 100%)}
.g2{left:444px;width:321px;background:linear-gradient(180deg,#f1f1f1 0%,#e2e0dc 45%,#6b3a24 62%,#4a2314 100%)}
.g3{left:774px;width:324px;background:linear-gradient(180deg,#f4f4f4 0%,#9fcbe2 35%,#d9e4e9 60%,#b8a995 100%)}
.arrow-l{left:64px;top:1772px}
.arrow-r{left:1116px;top:1772px}

/* footer */
.footer{left:0;top:1976px;width:1200px;height:298px;background:var(--footer);font-family:'Open Sans',sans-serif;color:var(--footer-text)}
.footer h4{position:absolute;top:60px;color:#fff;font-size:18px;font-weight:600}
.footer .rule{position:absolute;top:48px;width:1px;height:190px;background:#3a3a3a}
.footer ul{position:absolute;top:106px;list-style:none;font-size:13.5px;line-height:24px;color:#fff}
.footer .contact{position:absolute;left:312px;top:106px;font-size:13.5px;line-height:24px;color:#cfcfcf}
.footer .news{position:absolute;left:611px;top:108px;width:280px;font-size:12px;line-height:22px}
.footer .news-form{position:absolute;left:611px;top:2150px;display:flex}
.news-input{position:absolute;left:611px;top:174px;width:234px;height:33px;background:#fff;color:#777;font-size:12px;font-style:italic;padding:9px 12px}
.news-go{position:absolute;left:845px;top:174px;width:45px;height:33px;background:var(--ocean);color:#fff;font-size:12px;font-weight:600;display:flex;align-items:center;justify-content:center}
.social{position:absolute;left:992px;top:120px;font-size:13.5px;line-height:31px;color:#fff}
.social li{list-style:none;display:flex;align-items:center;gap:10px}
.social .mark{width:11px;height:11px;border-radius:50%;background:var(--sky)}
.basebar{left:0;top:2274px;width:1200px;height:40px;background:var(--footer-base);color:#7a7a7a;font-family:'Open Sans',sans-serif;font-size:12.5px;padding:11px 99px}
</style>
</head>
<body>

<div class="abs topbar">
  <span style="left:99px">USD ($) <svg width="8" height="6" viewBox="0 0 8 6"><path d="M1 1l3 3 3-3" stroke="#fff" fill="none" stroke-width="1.4"/></svg></span>
  <span style="left:184px">English <svg width="8" height="6" viewBox="0 0 8 6"><path d="M1 1l3 3 3-3" stroke="#fff" fill="none" stroke-width="1.4"/></svg></span>
  <span style="left:922px">? Help</span>
  <span style="left:995px"><svg width="10" height="11" viewBox="0 0 10 11"><circle cx="5" cy="3" r="2.6" fill="#fff"/><path d="M0 11c0-4 10-4 10 0z" fill="#fff"/></svg> Log in / Register</span>
</div>

<div class="abs hero-backdrop" role="img" aria-label="Bright sky with clouds above a turquoise sea"></div>

<div class="abs brand"><span class="dot"></span>Tidewell Glass Care</div>

<nav class="abs nav">
  <a class="active">HOME</a><span class="slash"></span>
  <a>ABOUT US</a><span class="slash"></span>
  <a>SERVICES</a><span class="slash"></span>
  <a>GALLERY</a><span class="slash"></span>
  <a style="padding-right:0">CONTACTS</a>
</nav>

<svg class="abs slider" viewBox="0 0 1002 530" role="img" aria-label="Bright living room with a white sofa and chair before floor-to-ceiling windows facing the ocean">
  <defs>
    <linearGradient id="room" x1="0" y1="0" x2="0" y2="1">
      <stop offset="0" stop-color="#cfe9f6"/>
      <stop offset="0.35" stop-color="#5fbfe6"/>
      <stop offset="0.5" stop-color="#2b9fd4"/>
      <stop offset="0.7" stop-color="#d9dde0"/>
      <stop offset="1" stop-color="#9aa3a6"/>
    </linearGradient>
  </defs>
  <path d="M3 3H999V447Q501 607 3 447Z" fill="url(#room)" stroke="#fff" stroke-width="6"/>
</svg>

<div class="abs slider-title">CLEANING IN CAYMAN ISLANDS</div>
<div class="abs search"><div class="field">Search For Your Text</div><div class="go">Let's Go!</div></div>
<div class="abs pager">
  <svg width="8" height="10" viewBox="0 0 8 10"><path d="M6 1L2 5l4 4" stroke="#222" stroke-width="2" fill="none"/></svg>
  <svg width="8" height="10" viewBox="0 0 8 10"><path d="M2 1l4 4-4 4" stroke="#222" stroke-width="2" fill="none"/></svg>
</div>

<h1 class="abs welcome-title">WELCOME TO TIDEWELL GLASS CARE</h1>
<p class="abs welcome-text">There are many variations of passages of Lorem Ipsum available, but the majority have suffered alteration in some form, by injected humour, or randomised words which don't look even slightly believable. If you are going to use a passage of Lorem Ipsum.</p>
<div class="abs down"><svg width="10" height="18" viewBox="0 0 10 18"><path d="M5 1v15M1 12l4 4 4-4" stroke="var(--deep)" stroke-width="2" fill="none"/></svg></div>

<section class="abs service" style="left:99px">
  <svg class="head" width="314" height="98" viewBox="0 0 314 98"><path d="M0 0Q157 20 314 30V98H0Z" fill="var(--ocean)"/></svg>
  <div class="title">WINDOW CLEANING</div>
  <div class="body">
    <svg class="icon" viewBox="0 0 80 82" fill="none" stroke="#333" stroke-width="3">
      <rect x="4" y="6" width="72" height="70"/>
      <path d="M4 6L22 14V68L4 76M76 6L58 14V68L76 76"/>
      <rect x="22" y="14" width="36" height="54"/>
    </svg>
    <p>Doloremque laudantium, totam rem aperiam, eaqu quae ab illo inventore veritatis et quasi architecto beatae vitae dicta sunt explicabo. Nemo ipsam voluptatem quia voluptas.</p>
    <div class="btn">READ MORE</div>
  </div>
</section>

<section class="abs service" style="left:443px">
  <svg class="head" width="314" height="98" viewBox="0 0 314 98"><path d="M0 14Q157 44 314 14V98H0Z" fill="var(--ocean)"/></svg>
  <div class="title">CEILING FANS CLEANING</div>
  <div class="body">
    <svg class="icon" viewBox="0 0 100 100" style="left:107px;width:100px;height:100px;top:18px" fill="#333">
      <rect x="43" y="2" width="14" height="34" rx="7"/>
      <rect x="43" y="64" width="14" height="34" rx="7"/>
      <rect x="2" y="43" width="34" height="14" rx="7"/>
      <rect x="64" y="43" width="34" height="14" rx="7"/>
      <rect x="36" y="48" width="28" height="4"/>
      <rect x="48" y="36" width="4" height="28"/>
      <circle cx="50" cy="50" r="7"/>
    </svg>
    <p>Doloremque laudantium, totam rem aperiam, eaqu quae ab illo inventore veritatis et quasi architecto beatae vitae dicta sunt explicabo. Nemo ipsam voluptatem quia voluptas.</p>
    <div class="btn">READ MORE</div>
  </div>
</section>

<section class="abs service" style="left:787px">
  <svg class="head" width="314" height="98" viewBox="0 0 314 98"><path d="M0 30Q157 20 314 0V98H0Z" fill="var(--ocean)"/></svg>
  <div class="title">MIRRORS CLEANING</div>
  <div class="body">
    <svg class="icon" viewBox="0 0 90 80" style="left:112px;width:90px" fill="#333">
      <path d="M4 12L36 40L4 68Z M11 27V53L25 40Z" fill-rule="evenodd"/>
      <rect x="42" y="4" width="5" height="72"/>
      <path d="M86 12L54 40L86 68Z"/>
    </svg>
    <p>Doloremque laudantium, totam rem aperiam, eaqu quae ab illo inventore veritatis et quasi architecto beatae vitae dicta sunt explicabo. Nemo ipsam voluptatem quia voluptas.</p>
    <div class="btn">READ MORE</div>
  </div>
</section>

<h2 class="abs about-title">ABOUT US</h2>
<p class="abs about-text">There are many variations of passages of Lorem Ipsum available, but the majority have suffered alteration in some form, by injected humour, or randomised words which don't look even slightly believable. If you are going to use a passage of Lorem Ipsum, you need to be sure there isn't anything embarrassing hidden in the middle of text. All the Lorem Ipsum generators on the Internet tend to repeat predefined chunks as necessary, making this the first true generator on the Internet. It uses a dictionary of over 200 Latin words, combined with a handful of model sentence structures, to generate Lorem Ipsum which looks reasonable.</p>
<div class="abs btn about-btn">READ MORE</div>
<div class="abs video" role="img" aria-label="Video still of a hand wiping a window with a blue cloth and a spray bottle"></div>
<div class="abs play"><svg width="26" height="30" viewBox="0 0 26 30"><path d="M2 1L25 15L2 29Z" fill="#fff" stroke="#ddd"/></svg></div>

<h2 class="abs gallery-title">OUR GALLERY</h2>
<svg class="abs arrow-l" width="20" height="80" viewBox="0 0 20 80"><path d="M18 2L2 40L18 78" stroke="#c8c8c8" stroke-width="1.5" fill="none"/></svg>
<div class="abs shot g1" role="img" aria-label="Squeegee clearing soapy glass"></div>
<div class="abs shot g2" role="img" aria-label="Vacuum cleaner on a polished wooden floor"></div>
<div class="abs shot g3" role="img" aria-label="Bright bedroom with glass walls overlooking the sea"></div>
<svg class="abs arrow-r" width="20" height="80" viewBox="0 0 20 80"><path d="M2 2L18 40L2 78" stroke="#c8c8c8" stroke-width="1.5" fill="none"/></svg>

<footer class="abs footer">
  <h4 style="left:99px">SEAGRAPE</h4>
  <ul style="left:99px"><li>Home</li><li>About US</li><li>Services</li><li>Gallery</li><li>Contacts</li></ul>
  <span class="rule" style="left:267px"></span>

  <h4 style="left:312px">CONTACT US</h4>
  <div class="contact">
    Seagrape Island<br>
    Mariner Lane 8 4410 Lindwald,<br>
    <span style="color:var(--sky)">&#9993;</span> @Tidewell Glass Care.com<br>
    <span style="color:var(--sky)">&#9742;</span> +41 41 552 08 37
  </div>
  <span class="rule" style="left:555px"></span>

  <h4 style="left:611px">SIGN TO NEWSLETTER</h4>
  <p class="news">Join our confidential network and be the first job listings for Connecticut military.</p>
  <div class="news-input">Name...</div>
  <div class="news-go">GO!</div>
  <span class="rule" style="left:925px"></span>

  <h4 style="left:992px">FOLLOW US</h4>
  <ul class="social">
    <li><span class="mark"></span>Shorebook</li>
    <li><span class="mark"></span>chirpline</li>
    <li><span class="mark"></span>reelcast</li>
  </ul>
</footer>
<div class="abs basebar">Impressum | Tidewell Glass Care © 2014, Alle Rechte vorbehalten</div>

</body>
</html>
```